Las Vegas transportation company needs a dynamic design for business cards

We are a transportation management company based in Las Vegas specializing in operating and maintaining public transit systems. We want to keep our existing logo but would like to design business cards that feature one or more transit systems (e.g. monorail, train, bus) and maybe also the Las Vegas landscape.

```html
<!DOCTYPE html>
<html lang="en">
<head>
<meta charset="utf-8">
<title>Mesa Transit Group – Business Card</title>
<link href="https://fonts.googleapis.com/css2?family=Montserrat:wght@500;600;700;800&display=swap" rel="stylesheet">
<style>
  :root {
    --canvas: #c9c9c9;
    --white: #ffffff;
    --navy: #0c1d62;
    --sky: #8dbbeb;
    --logo-grey: #8e9099;
    --night-top: #0b0d22;
    --night-mid: #2a1f48;
    --night-glow: #b8652a;
    --night-low: #5a2a1c;
  }
  * { box-sizing: border-box; margin: 0; padding: 0; }
  html, body { width: 1200px; height: 800px; overflow: hidden; }
  body {
    background: var(--canvas);
    font-family: "Montserrat", Arial, sans-serif;
    display: flex;
    align-items: center;
    justify-content: center;
    gap: 30px;
  }
  .card {
    width: 550px;
    height: 314px;
    position: relative;
    overflow: hidden;
    box-shadow: 0 6px 18px rgba(0,0,0,0.25);
  }

  /* Front */
  .card-front { background: var(--white); display: flex; flex-direction: column; }
  .front-logo-zone {
    height: 112px;
    display: flex;
    align-items: center;
    justify-content: center;
    gap: 12px;
  }
  .brand-dot { width: 18px; height: 18px; border-radius: 50%; background: var(--sky); }
  .brand-name {
    font-size: 30px;
    font-weight: 600;
    letter-spacing: 2px;
    color: var(--navy);
  }
  .front-info-band {
    height: 138px;
    background: var(--navy);
    display: flex;
    align-items: center;
    padding: 0 34px;
  }
  .holder { flex: 0 0 210px; }
  .holder-name {
    color: var(--white);
    font-size: 22px;
    font-weight: 800;
    letter-spacing: 0.5px;
  }
  .holder-title { color: var(--sky); font-size: 15px; font-weight: 500; margin-top: 4px; }
  .info-divider { width: 1px; height: 70px; background: rgba(255,255,255,0.4); margin: 0 22px; }
  .contact-list { list-style: none; display: flex; flex-direction: column; gap: 8px; }
  .contact-item {
    display: flex; align-items: center; gap: 9px;
    color: var(--white); font-size: 14px; font-weight: 500;
  }
  .contact-item svg { width: 15px; height: 15px; flex: none; }
  .front-address-band {
    flex: 1;
    background: var(--sky);
    display: flex;
    align-items: center;
    padding: 0 34px;
    color: var(--navy);
    font-size: 15px;
    font-weight: 500;
  }

  /* Back */
  .card-back { background: var(--night-top); }
  .cityscape {
    position: absolute; inset: 0;
    background: linear-gradient(180deg, var(--night-top) 0%, var(--night-mid) 45%, var(--night-glow) 78%, var(--night-low) 100%);
  }
  .back-brand {
    position: absolute; top: 30px; right: 30px;
    display: flex; align-items: center; gap: 10px;
  }
  .back-brand .brand-name { color: var(--logo-grey); font-size: 26px; }
  .back-brand .brand-dot { background: var(--logo-grey); width: 15px; height: 15px; }
  .transit-badges {
    position: absolute; right: 40px; top: 100px;
    display: flex; flex-direction: column; gap: 14px; align-items: flex-end;
  }
  .transit-badge {
    width: 90px; height: 90px; border-radius: 50%;
    background: var(--navy);
    border: 3px solid var(--white);
    display: flex; align-items: center; justify-content: center;
  }
  .transit-badge:last-child { margin-right: -26px; }
  .transit-badge svg { width: 54px; height: 54px; }
</style>
</head>
<body>

<section class="card card-front" aria-label="Business card front">
  <div class="front-logo-zone">
    <span class="brand-dot"></span>
    <span class="brand-name">MESA TRANSIT GROUP</span>
  </div>
  <div class="front-info-band">
    <div class="holder">
      <p class="holder-name">DORIAN HALE</p>
      <p class="holder-title">Managing Director</p>
    </div>
    <span class="info-divider"></span>
    <ul class="contact-list">
      <li class="contact-item">
        <svg viewBox="0 0 16 16" fill="none" stroke="#fff" stroke-width="1.6"><path d="M4 2l2.5 3-1.5 1.5c1 2 2.5 3.5 4.5 4.5L11 9.5l3 2.5-1.5 2C7 13.5 2.5 9 2 3.5z"/></svg>
        044-555 010 222
      </li>
      <li class="contact-item">
        <svg viewBox="0 0 16 16" fill="none" stroke="#fff" stroke-width="1.6"><rect x="1.5" y="3.5" width="13" height="9"/><path d="M1.5 3.5L8 9l6.5-5.5"/></svg>
        info@mesatransit.com
      </li>
      <li class="contact-item">
        <svg viewBox="0 0 16 16" fill="none" stroke="#fff" stroke-width="1.4"><circle cx="8" cy="8" r="6.3"/><ellipse cx="8" cy="8" rx="2.8" ry="6.3"/><path d="M1.7 8h12.6M2.8 4.8h10.4M2.8 11.2h10.4"/></svg>
        www.mesatransit.com
      </li>
    </ul>
  </div>
  <div class="front-address-band">88 Canyon Loop Drive 89109, United States</div>
</section>

<section class="card card-back" aria-label="Business card back">
  <div class="cityscape" role="img" aria-label="Night view of the Las Vegas Strip with palm trees, casino lights and traffic"></div>
  <div class="back-brand">
    <span class="brand-dot"></span>
    <span class="brand-name">MESA TRANSIT GROUP</span>
  </div>
  <div class="transit-badges">
    <div class="transit-badge" aria-label="Bus">
      <svg viewBox="0 0 54 54" fill="none" stroke="#fff" stroke-width="3.5" stroke-linejoin="round">
        <rect x="10" y="6" width="34" height="36" rx="6"/>
        <path d="M10 26h34M27 8v18"/>
        <path d="M6 16v8M48 16v8"/>
        <circle cx="17" cy="34" r="2" fill="#fff"/><circle cx="37" cy="34" r="2" fill="#fff"/>
        <path d="M15 42v6M39 42v6"/>
      </svg>
    </div>
    <div class="transit-badge" aria-label="Train">
      <svg viewBox="0 0 54 54" fill="none" stroke="#fff" stroke-width="3.5" stroke-linejoin="round">
        <path d="M13 36V16c0-6 6-10 14-10s14 4 14 10v20z"/>
        <path d="M15 20h24"/>
        <circle cx="20" cy="29" r="2" fill="#fff"/><circle cx="34" cy="29" r="2" fill="#fff"/>
        <path d="M8 46h38M14 40l-4 6M40 40l4 6"/>
      </svg>
    </div>
  </div>
</section>

</body>
</html>
```